Satchel & Sundial needs new business card design

I need a new business card design. I'm looking for out-of-the-box design which represents the freedom of being a location independent entrepreneur.
I offer coaching, retreats and trips.
I would like to see designs with and without the photo.
Colors I use are black (#000000), green (#25A796) and brown (#D7C38C)
Website satchelandsundial.example

Target Market(s)

location independent entrepreneurs, digital nomads, people looking to swap the 9 to 5 for a lifestyle business

Industry/Entity Type

Business

Contact Information for Business Card

Dorota Falkner
Your Lifestyle Business Coach, Retreat & Trip Leader
http://satchelandsundial.example
hello@satchelandsundial.example
Live a life you don't need a holiday from

Font styles to use
Serif
Sans Serif

Requirements
Must have
• One side should contain only the logo. I would also consider having the "Live a life you don't need a holiday from" on that side too (depending on how it looks)
• Please show both sides on the designs.

```html
<!DOCTYPE html>
<html lang="en">
<head>
<meta charset="utf-8">
<title>Satchel &amp; Sundial — Business Card</title>
<link rel="stylesheet" href="https://fonts.googleapis.com/css2?family=Open+Sans:wght@400;600;700&display=swap">
<style>
  :root {
    --page: #ececec;
    --card-white: #ffffff;
    --card-black: #231f20;
    --teal: #25a796;
    --ink: #231f20;
    --paper-text: #ffffff;
  }
  * { box-sizing: border-box; margin: 0; padding: 0; }
  html, body {
    width: 1105px;
    height: 1200px;
    overflow: hidden;
    background: var(--page);
    font-family: "Open Sans", Arial, sans-serif;
  }
  .sheet {
    position: relative;
    width: 1105px;
    height: 1200px;
  }
  .card {
    position: absolute;
    left: 192px;
    width: 720px;
    height: 410px;
    overflow: hidden;
  }
  .card--front { top: 146px; background: var(--card-white); }
  .card--back { top: 602px; background: var(--card-black); }

  /* Front */
  .contact-panel {
    position: absolute;
    left: 0;
    top: 99px;
    width: 351px;
    height: 210px;
    background: var(--card-black);
    padding: 28px 0 0 30px;
    color: var(--paper-text);
  }
  .contact-panel__name {
    color: var(--teal);
    font-weight: 600;
    font-size: 24px;
    letter-spacing: 0.5px;
    text-transform: uppercase;
    line-height: 1;
    margin-bottom: 10px;
  }
  .contact-panel__role {
    font-size: 18px;
    line-height: 26px;
  }
  .contact-list {
    list-style: none;
    margin-top: 16px;
  }
  .contact-list__item {
    display: flex;
    align-items: center;
    gap: 9px;
    font-size: 18px;
    line-height: 28px;
  }
  .contact-list__icon { width: 16px; height: 16px; flex: none; }
  .accent-bar {
    position: absolute;
    right: 0;
    top: 99px;
    width: 17px;
    height: 210px;
    background: var(--teal);
  }
  .brand-name {
    position: absolute;
    font-weight: 600;
    white-space: nowrap;
    letter-spacing: 0.5px;
  }
  .brand-name--front {
    left: 382px;
    top: 180px;
    width: 306px;
    text-align: center;
    font-size: 33px;
    color: var(--ink);
  }

  /* Back */
  .social-row {
    position: absolute;
    top: 26px;
    right: 22px;
    display: flex;
    gap: 4px;
  }
  .social-row__tile {
    width: 24px;
    height: 24px;
    background: var(--teal);
  }
  .brand-name--back {
    left: 0;
    top: 170px;
    width: 720px;
    text-align: center;
    font-size: 44px;
    color: var(--paper-text);
  }
  .tagline {
    position: absolute;
    left: 0;
    top: 341px;
    width: 720px;
    text-align: center;
    font-size: 17px;
    color: var(--paper-text);
    text-transform: uppercase;
  }
</style>
</head>
<body>
<main class="sheet">
  <section class="card card--front" aria-label="Card front">
    <div class="contact-panel">
      <h1 class="contact-panel__name">Dorota Falkner</h1>
      <p class="contact-panel__role">Your Lifestyle Business Coach</p>
      <p class="contact-panel__role">Retreat &amp; Trip Leader</p>
      <ul class="contact-list">
        <li class="contact-list__item">
          <svg class="contact-list__icon" viewBox="0 0 16 16" aria-hidden="true">
            <rect x="1" y="3" width="14" height="10" fill="#25a796"/>
            <path d="M1 3 L8 9 L15 3" fill="none" stroke="#231f20" stroke-width="1.4"/>
          </svg>
          hello@satchelandsundial.example
        </li>
        <li class="contact-list__item">
          <svg class="contact-list__icon" viewBox="0 0 16 16" aria-hidden="true">
            <circle cx="8" cy="8" r="7" fill="#25a796"/>
            <path d="M1 8 H15 M8 1 C4 5 4 11 8 15 M8 1 C12 5 12 11 8 15" fill="none" stroke="#231f20" stroke-width="1"/>
          </svg>
          www.satchelandsundial.example
        </li>
      </ul>
    </div>
    <p class="brand-name brand-name--front">Satchel &amp; Sundial</p>
    <div class="accent-bar"></div>
  </section>

  <section class="card card--back" aria-label="Card back">
    <div class="social-row" aria-label="Social profiles">
      <span class="social-row__tile"></span>
      <span class="social-row__tile"></span>
      <span class="social-row__tile"></span>
    </div>
    <p class="brand-name brand-name--back">Satchel &amp; Sundial</p>
    <p class="tagline">Live a life you don’t need a holiday from</p>
  </section>
</main>
</body>
</html>
```